Social Media Graphics - Oakline Push REVISED

Create 6-7 individual social media graphics (square size) to encourage folks to join our online course called:

The Harvest Ledger Circle
How to Launch a Multi-Million Business From Scratch
Sign Up Today!

IMPORTANT: Make the largest and most prominent text on the graphic be: How to Launch a Multi-Million Business From Scratch

For the color scheme of the graphics, let's try a blue color palette; make sure the graphics appeal to both men and women

Make sure each graphic contains 1 of the 3 pics attached (crop pic as needed); and make sure one of the graphics is all TEXT only.

Target Market(s)

men and women looking to start a business

Industry/Entity Type

Entrepreneurship

Colors
0054AA
0677BA
7BADD7
CADEEF
E8F1F8

Requirements
Must have
• All the text and use the 3 pics provided; one graphic can be all text; Simple, modern design that's easy to read

```html
<!DOCTYPE html>
<html lang="en">
<head>
<meta charset="UTF-8">
<title>The Harvest Ledger Circle – Sign Up</title>
<link href="https://fonts.googleapis.com/css2?family=Anton&family=Archivo+Black&display=swap" rel="stylesheet">
<style>
  :root {
    --blue-light: #2aa3e0;
    --blue-mid: #0677BA;
    --blue-deep: #0a3d9a;
    --blue-navy: #07237a;
    --white: #ffffff;
    --blue-pale: #CADEEF;
    --button-fill: #221f38;
    --button-ring: #a48d5c;
  }
  * { margin: 0; padding: 0; box-sizing: border-box; }
  html, body { width: 1200px; height: 1200px; overflow: hidden; }
  body { background: var(--blue-navy); }
  .social-graphic {
    position: relative;
    width: 1200px;
    height: 1200px;
    overflow: hidden;
    background:
      radial-gradient(ellipse 70% 55% at 50% 22%, var(--blue-light) 0%, rgba(42,163,224,0) 70%),
      linear-gradient(180deg, var(--blue-mid) 0%, var(--blue-deep) 55%, var(--blue-navy) 100%);
  }
  .frame {
    position: absolute;
    inset: 30px;
    border: 4px solid rgba(255,255,255,0.92);
  }
  .hosts-photo {
    position: absolute;
    left: 270px;
    top: 56px;
    width: 660px;
    height: 540px;
    background: linear-gradient(180deg, #1b2a4a 0%, #1d3f7a 60%, rgba(15,60,150,0) 100%);
    border-radius: 240px 240px 0 0;
    opacity: 0.85;
  }
  .course-name {
    position: absolute;
    left: 0;
    right: 0;
    top: 584px;
    text-align: center;
    font-family: 'Archivo Black', sans-serif;
    font-size: 42px;
    line-height: 50px;
    letter-spacing: 1px;
    color: var(--blue-pale);
    text-transform: uppercase;
  }
  .headline {
    position: absolute;
    left: 0;
    right: 0;
    top: 646px;
    text-align: center;
    color: var(--white);
    font-family: 'Anton', sans-serif;
    font-weight: 400;
    font-size: 100px;
    line-height: 100px;
    text-transform: uppercase;
  }
  .headline span { display: block; white-space: nowrap; }
  .cta-button {
    position: absolute;
    left: 410px;
    top: 1046px;
    width: 380px;
    height: 94px;
    border-radius: 47px;
    background: var(--button-fill);
    border: 5px solid var(--button-ring);
    display: flex;
    align-items: center;
    justify-content: center;
    font-family: 'Anton', sans-serif;
    font-size: 56px;
    letter-spacing: -1px;
    color: var(--white);
    text-transform: uppercase;
  }
</style>
</head>
<body>
  <main class="social-graphic">
    <div class="frame"></div>
    <div class="hosts-photo" role="img" aria-label="Photo of the two course hosts smiling, a man in a black turtleneck with arms crossed and a woman in a blue velvet blazer"></div>
    <p class="course-name">The Harvest Ledger Circle</p>
    <h1 class="headline">
      <span>How to launch a</span>
      <span>multi-million</span>
      <span>business from scratch</span>
    </h1>
    <div class="cta-button">Sign up today!</div>
  </main>
</body>
</html>
```